Animal Eye Clinic needs a Business card

We are a new veterinary ophthalmology practice (Ridgeline Pet Vision Care) and we need a business card designed. We only see animal eyes - we are not a regular veterinary clinic. We already have a logo. We are looking for a professional, good looking business card to hand out to our clients. We are looking for something simple but professional and contemporary. Our logo is likely the only picture/graphic that needs to be on the card.
Updates

Contact Information for Business Card

Delia Vossman, BSc, DVM, MSc, DipACVO
Veterinary Ophthalmologist

Phone: 250.418.3927
Email: ridgelinepetvisioncare@mailbox-example.net
Website: ridgelinepetvisioncare-example.net
Address: 1874 Thornbury Rd
Larchmere, NL, V1X 4M9

Colors

Designer to choose colors to be used in the design.

Requirements
Must have
• Our logo (attached)

```html
<!DOCTYPE html>
<html lang="en">
<head>
<meta charset="utf-8">
<title>Ridgeline Pet Vision Care – Business Card</title>
<link href="https://fonts.googleapis.com/css2?family=Roboto:wght@300;400;500;700&display=swap" rel="stylesheet">
<style>
  :root {
    --backdrop: #3b322d;
    --card: #2e2f31;
    --teal: #1c9fae;
    --ink: #e9eaeb;
    --emboss: #3a3b3e;
    --rule: #bfc2c4;
  }
  * { box-sizing: border-box; margin: 0; padding: 0; }
  html, body { width: 1200px; height: 787px; overflow: hidden; }
  body {
    background: var(--backdrop);
    font-family: "Roboto", Arial, sans-serif;
    position: relative;
  }
  .card {
    position: absolute;
    width: 540px;
    height: 309px;
    background: var(--card);
    border: 2px solid var(--teal);
    border-radius: 3px;
    box-shadow: 0 10px 24px rgba(0,0,0,0.35);
  }
  .card--front { left: 40px; top: 239px; }
  .card--back { left: 620px; top: 239px; }

  .front-brand {
    position: absolute;
    left: 0; right: 0; top: 118px;
    display: flex; align-items: center; justify-content: center; gap: 14px;
  }
  .brand-dot {
    width: 46px; height: 46px; border-radius: 50%;
    background: var(--emboss);
    flex: none;
  }
  .front-brand .brand-name {
    color: var(--emboss);
    font-weight: 700;
    font-size: 26px;
    letter-spacing: 0.5px;
    text-transform: uppercase;
    line-height: 1.05;
  }

  .back-brand {
    position: absolute;
    right: 26px; top: 30px;
    display: flex; align-items: center; gap: 10px;
  }
  .back-brand .brand-dot { width: 34px; height: 34px; background: var(--teal); }
  .back-brand .brand-name {
    color: var(--teal);
    font-weight: 700;
    font-size: 17px;
    text-transform: uppercase;
    line-height: 1.05;
  }

  .person { position: absolute; left: 28px; top: 100px; right: 28px; }
  .person-name { color: var(--teal); font-size: 15px; font-weight: 400; }
  .person-name strong { font-weight: 700; }
  .person-title { color: var(--ink); font-size: 13px; font-weight: 300; margin-top: 3px; }
  .rule { height: 1px; background: var(--rule); margin-top: 10px; opacity: 0.8; }

  .contact-list { position: absolute; left: 28px; top: 172px; list-style: none; }
  .contact-list li {
    color: var(--ink); font-size: 12.5px; font-weight: 300;
    display: flex; align-items: center; gap: 7px; margin-bottom: 5px;
  }
  .contact-list svg { width: 10px; height: 10px; fill: var(--teal); flex: none; }
  .contact-list .web-accent { color: var(--teal); }

  .address {
    position: absolute; right: 28px; bottom: 18px;
    color: var(--ink); font-size: 13px; font-weight: 300; line-height: 1.35;
  }
</style>
</head>
<body>
  <section class="card card--front" aria-label="Card front">
    <div class="front-brand">
      <span class="brand-dot"></span>
      <span class="brand-name">Ridgeline<br>Pet Vision Care</span>
    </div>
  </section>

  <section class="card card--back" aria-label="Card back">
    <div class="back-brand">
      <span class="brand-dot"></span>
      <span class="brand-name">Ridgeline<br>Pet Vision Care</span>
    </div>

    <div class="person">
      <p class="person-name"><strong>Delia Vossman,</strong> BSc, DVM, MSc, DipACVO</p>
      <p class="person-title">Veterinary Ophthalmologist</p>
      <div class="rule"></div>
    </div>

    <ul class="contact-list">
      <li>
        <svg viewBox="0 0 10 10" aria-hidden="true"><path d="M2 0.5 L3.6 2.6 L2.8 3.6 C3.4 5 4.8 6.4 6.3 7.1 L7.4 6.3 L9.5 7.9 L8.4 9.5 C4.3 9.3 0.7 5.7 0.5 1.6 Z"/></svg>
        250.418.3927
      </li>
      <li>
        <svg viewBox="0 0 10 10" aria-hidden="true"><path d="M0.5 2 H9.5 V8.5 H0.5 Z M0.8 2.3 L5 5.6 L9.2 2.3" stroke="#2e2f31" stroke-width="0.8"/></svg>
        ridgelinepetvisioncare@mailbox-example.net
      </li>
      <li>
        <svg viewBox="0 0 10 10" aria-hidden="true"><circle cx="5" cy="5" r="4.5"/><path d="M0.5 5 H9.5 M5 0.5 C2.6 3 2.6 7 5 9.5 M5 0.5 C7.4 3 7.4 7 5 9.5" stroke="#2e2f31" stroke-width="0.7" fill="none"/></svg>
        <span>www.<span class="web-accent">ridgelinepetvisioncare-example</span>.net</span>
      </li>
    </ul>

    <p class="address">1874 Thornbury Rd<br>Larchmere, NL, V1X 4M9</p>
  </section>
</body>
</html>
```